SOLVE Study flyer

I need help designing a flyer for a research study that will include brain imaging in adolescents. The info is in the attached document. The study is called the Sequoia Outlook Lantern Valley Echo (SOLVE) study. Ideally this would be returned as a document that I can edit in the future as we will have several new recruitment phases (different age groups, etc. I also would love to have a logo designed as part of this project, but I recognize that might be a separate design request.

```html
<!DOCTYPE html>
<html lang="en">
<head>
<meta charset="utf-8">
<title>SOLVE Study Flyer</title>
<link href="https://fonts.googleapis.com/css2?family=Poppins:ital,wght@0,400;0,500;0,600;0,800;1,800&display=swap" rel="stylesheet">
<style>
  :root {
    --navy: #0e3370;
    --navy-deep: #0b2a5c;
    --blue: #0a7fd8;
    --bright-blue: #1b8fe6;
    --ink: #0e3370;
    --text: #1d2433;
    --white: #ffffff;
    --pill: #222222;
  }
  * { margin: 0; padding: 0; box-sizing: border-box; }
  html, body { width: 927px; height: 1200px; overflow: hidden; background: var(--white); }
  body { font-family: "Poppins", sans-serif; }
  .flyer { position: relative; width: 927px; height: 1200px; overflow: hidden; background: var(--white); }

  .hero-photo {
    position: absolute; left: 0; top: 0; width: 927px; height: 720px;
    background:
      linear-gradient(90deg, rgba(11,31,66,0.95) 0%, rgba(20,40,70,0.75) 38%, rgba(120,120,130,0.15) 60%, rgba(0,0,0,0) 75%),
      linear-gradient(160deg, #3b4a63 0%, #6f6a7e 35%, #b9a9c9 55%, #d8cfd6 75%, #c9b7ad 100%);
    clip-path: polygon(0 0, 100% 0, 100% 702px, 356px 640px, 0 600px);
  }
  .shapes { position: absolute; left: 0; top: 0; }

  .abs { position: absolute; }

  .brand { left: 672px; top: 22px; width: 200px; text-align: center; color: var(--navy); }
  .brand-name { font-weight: 800; font-size: 44px; line-height: 1; letter-spacing: 1px; }
  .brand-full { font-size: 12.5px; font-weight: 400; line-height: 1.6; margin-top: 6px; color: var(--text); }

  .headline { left: 29px; top: 88px; width: 470px; color: var(--white); font-weight: 800; font-size: 51px; line-height: 0.96; letter-spacing: -0.5px; }
  .subhead { left: 29px; top: 255px; width: 420px; color: var(--white); font-weight: 800; font-style: italic; font-size: 35px; line-height: 1.24; }
  .intro { left: 29px; top: 398px; width: 430px; color: var(--white); font-weight: 600; font-size: 14.6px; line-height: 1.66; }

  .panel-title { left: 55px; top: 640px; color: var(--white); font-weight: 800; font-size: 41px; line-height: 1.1; }
  .checklist { list-style: none; }
  .checklist li { position: relative; padding-left: 27px; }
  .checklist li svg { position: absolute; left: 0; top: 5px; }
  .participation { left: 56px; top: 800px; width: 270px; color: var(--white); font-size: 14.4px; line-height: 1.5; letter-spacing: 0.3px; }
  .participation li { margin-bottom: 16px; }
  .participation li:nth-child(2) { margin-bottom: 26px; }

  .eligible-title { left: 381px; top: 724px; color: var(--ink); font-weight: 800; font-size: 28px; line-height: 1.2; }
  .eligible { left: 381px; top: 775px; width: 430px; color: var(--text); font-size: 14.4px; line-height: 1.5; font-weight: 500; letter-spacing: 0.3px; }
  .eligible li { margin-bottom: 10px; }
  .interested { left: 382px; top: 858px; color: var(--ink); font-weight: 800; font-size: 24px; line-height: 1.42; }

  .contact { left: 381px; top: 940px; display: flex; align-items: center; gap: 12px; }
  .contact-label { font-weight: 600; font-size: 16.5px; color: var(--text); line-height: 1.2; }
  .contact-email { font-weight: 500; font-size: 19.5px; color: var(--blue); letter-spacing: 0.4px; }

  .pill { left: 356px; top: 1006px; width: 360px; height: 54px; background: var(--pill); border-radius: 0 30px 30px 0; color: var(--white); font-weight: 800; font-size: 22px; display: flex; align-items: center; padding-left: 25px; }

  .footer-contact { left: 440px; top: 1120px; width: 405px; text-align: right; }
  .footer-label { color: var(--bright-blue); font-weight: 600; font-size: 16.5px; line-height: 1.2; }
  .footer-email { color: var(--white); font-weight: 500; font-size: 20px; letter-spacing: 0.3px; line-height: 1.5; white-space: nowrap; }
  .footer-icon { left: 858px; top: 1124px; }
  .code { left: 898px; top: 1180px; color: var(--white); font-size: 8px; }
</style>
</head>
<body>
<div class="flyer">
  <div class="hero-photo" role="img" aria-label="Photo of a mother comforting her daughter in a hoodie on a bed, with a university tower in the background"></div>

  <svg class="shapes" width="927" height="1200" viewBox="0 0 927 1200" aria-hidden="true">
    <polygon points="531,0 927,0 927,73 778,193" fill="var(--white)"/>
    <polyline points="531,0 778,193 927,73" fill="none" stroke="var(--blue)" stroke-width="7" stroke-linejoin="round"/>
    <polygon points="0,592 32,564 32,640 0,636" fill="var(--blue)"/>
    <polygon points="0,600 32,604 32,640 0,636" fill="var(--white)"/>
    <polygon points="0,636 32,640 32,1102 0,1102" fill="var(--white)"/>
    <polygon points="32,564 356,603 356,1102 32,1102" fill="var(--navy)"/>
    <polygon points="356,640 927,702 927,720 356,652" fill="var(--blue)"/>
    <polygon points="0,1124 927,1050 927,1060 0,1138" fill="var(--blue)"/>
    <polygon points="0,1148 927,1062 927,1200 0,1200" fill="var(--navy-deep)"/>
    <polygon points="0,1130 356,1102 356,1112 0,1142" fill="var(--white)"/>
  </svg>

  <div class="abs brand">
    <div class="brand-name">SOLVE</div>
    <div class="brand-full">Sequoia Outlook Lantern<br>Valley Echo</div>
  </div>

  <h1 class="abs headline">Are you the parent of a child age 10-17?</h1>
  <h2 class="abs subhead">Do they worry or overthink negative emotions?</h2>
  <p class="abs intro">Lantern Valley University researchers are seeking girls age 10-17 for a study about brain activity in emotions and decision-making and how they relate to puberty, anxiety and depression.</p>

  <h2 class="abs panel-title">Study<br>Participation<br>Involves</h2>
  <ul class="abs checklist participation">
    <li><svg width="15" height="12" viewBox="0 0 15 12"><path d="M1.5 6.5 L5.5 10 L13.5 1.5" fill="none" stroke="var(--bright-blue)" stroke-width="2.6"/></svg>One one-hour interview (online or in-person) where your child will discuss their thoughts</li>
    <li><svg width="15" height="12" viewBox="0 0 15 12"><path d="M1.5 6.5 L5.5 10 L13.5 1.5" fill="none" stroke="var(--bright-blue)" stroke-width="2.6"/></svg>Online questionnaires (parent and child)</li>
    <li><svg width="15" height="12" viewBox="0 0 15 12"><path d="M1.5 6.5 L5.5 10 L13.5 1.5" fill="none" stroke="var(--bright-blue)" stroke-width="2.6"/></svg>One two-hour visit where your child will complete an MRI scan, answer questions about their puberty stage, and have a small hair sample taken to study puberty hormones.</li>
  </ul>

  <h2 class="abs eligible-title">Your Child Maybe Eligible if They</h2>
  <ul class="abs checklist eligible">
    <li><svg width="15" height="12" viewBox="0 0 15 12"><path d="M1.5 6.5 L5.5 10 L13.5 1.5" fill="none" stroke="var(--bright-blue)" stroke-width="2.6"/></svg>Are age 10-17</li>
    <li><svg width="15" height="12" viewBox="0 0 15 12"><path d="M1.5 6.5 L5.5 10 L13.5 1.5" fill="none" stroke="var(--bright-blue)" stroke-width="2.6"/></svg>Have not been diagnosed with psychosis, learning problems, or autism.</li>
  </ul>
  <h2 class="abs interested">Interested in participating?<br>Want more information?</h2>

  <div class="abs contact">
    <svg width="42" height="42" viewBox="0 0 42 42" aria-hidden="true">
      <circle cx="21" cy="21" r="21" fill="var(--bright-blue)"/>
      <rect x="13" y="15" width="16" height="12" rx="1.5" fill="var(--white)"/>
      <path d="M13 16 L21 22 L29 16" fill="none" stroke="var(--bright-blue)" stroke-width="1.6"/>
    </svg>
    <div>
      <div class="contact-label">Please Contact Us!</div>
      <div class="contact-email">solvestudy@lanternvalley.edu</div>
    </div>
  </div>

  <div class="abs pill">Compensation up to $140</div>

  <div class="abs footer-contact">
    <div class="footer-label">Please Contact Us!</div>
    <div class="footer-email">solvestudy@lanternvalley.edu</div>
  </div>
  <svg class="abs footer-icon" width="42" height="42" viewBox="0 0 42 42" aria-hidden="true">
    <circle cx="21" cy="21" r="21" fill="var(--bright-blue)"/>
    <rect x="13" y="15" width="16" height="12" rx="1.5" fill="var(--white)"/>
    <path d="M13 16 L21 22 L29 16" fill="none" stroke="var(--bright-blue)" stroke-width="1.6"/>
  </svg>
  <div class="abs code">x10</div>
</div>
</body>
</html>
```